Business Card Design Project : Ridgeline Press

In preparation for market launch, Tamarind's Ridgeline Press require the development of a business card. Ridgeline Press is a Community online publishing web portal. We provide the the city of Whistler located in B.C. (Canada) business directories, News, Classified ads, News, Events and blogs etc.

The main focus of the brand is to help local businesses to corporate with their online advertisement and marketing. Meeting our clients face to face is a must (B2B).

Target Market(s)

The target market is B2B customers. Business Owners to Marketing, advertising Managers

Industry/Entity Type

Business

Requirements
Must have
• - The business card will be two sided.
the BACK side will have our logo which consist of (icon, url,slogan) submited. The logo will be middle and centred.

The FRONT side should have company details:

Company Legal Name: TAMARIND RIDGELINE MEDIA

Owen Farsk
Director of Sales & Marketing

www.tamarindridgeline.biz
owen@tamarindridgeline.biz

Phone: 604 317 8842
#2714 - 582 E. Halvern St.
Vancouver, B.C. V7K2R4 Canada
Nice to have
• - For the "FRONT" side of our business card. You can separate or re-arrange with our logo components (icon, logo,slogan). It does not have to be together.

Also our company legal name is rather long so arrange or organize the name in a way to make it shorter. Your experience and creativity will have to come in play.
Should not have
• should not have other colors beside logo color and black text (2 colors). Also nothing Three dimensional

```html
<!DOCTYPE html>
<html lang="en">
<head>
<meta charset="utf-8">
<title>Ridgeline Press – Business Card</title>
<link rel="stylesheet" href="https://fonts.googleapis.com/css2?family=Source+Sans+3:wght@400;600;700&display=swap">
<style>
  :root {
    --brand-blue: #3a8cf0;
    --ink: #111111;
    --card-white: #ffffff;
    --backdrop: #e9eaea;
    --divider: #7fb4f5;
  }
  * { box-sizing: border-box; margin: 0; padding: 0; }
  html, body {
    width: 1200px;
    height: 606px;
    overflow: hidden;
  }
  body {
    background: var(--backdrop);
    font-family: "Source Sans 3", Arial, sans-serif;
    color: var(--ink);
    position: relative;
  }
  .card {
    position: absolute;
    top: 153px;
    width: 525px;
    height: 300px;
    border-radius: 4px;
    box-shadow: 0 1px 3px rgba(0,0,0,0.18);
    overflow: hidden;
  }

  /* Front */
  .card--front {
    left: 50px;
    background: var(--card-white);
  }
  .front__company {
    position: absolute;
    left: 30px;
    top: 30px;
    font-weight: 700;
    font-size: 19px;
    letter-spacing: 0.2px;
  }
  .front__slogan {
    position: absolute;
    left: 30px;
    top: 54px;
    font-size: 17px;
    color: var(--brand-blue);
  }
  .front__divider {
    position: absolute;
    left: 272px;
    top: 24px;
    width: 1px;
    height: 252px;
    background: var(--divider);
  }
  .front__brand {
    position: absolute;
    left: 30px;
    top: 110px;
    width: 222px;
    text-align: center;
    display: flex;
    align-items: center;
    justify-content: center;
    gap: 10px;
    font-weight: 700;
    font-size: 26px;
    color: var(--brand-blue);
  }
  .brand-dot {
    width: 16px;
    height: 16px;
    border-radius: 50%;
    background: var(--brand-blue);
    flex: none;
  }
  .front__person {
    position: absolute;
    left: 30px;
    top: 208px;
    width: 232px;
    text-align: center;
  }
  .person__name {
    font-size: 21px;
    font-weight: 600;
  }
  .person__title {
    font-size: 15px;
    margin-top: 2px;
  }
  .front__contact {
    position: absolute;
    right: 28px;
    top: 34px;
    text-align: right;
    font-size: 15px;
    line-height: 1.35;
  }
  .front__online {
    position: absolute;
    right: 28px;
    bottom: 34px;
    text-align: right;
    font-size: 15px;
    line-height: 1.35;
  }

  /* Back */
  .card--back {
    left: 625px;
    background: var(--brand-blue);
    color: var(--card-white);
    text-align: center;
  }
  .back__url {
    position: absolute;
    top: 30px;
    left: 0;
    right: 0;
    font-weight: 700;
    font-size: 28px;
  }
  .back__brand {
    position: absolute;
    top: 118px;
    left: 0;
    right: 0;
    display: flex;
    align-items: center;
    justify-content: center;
    gap: 14px;
    font-weight: 700;
    font-size: 44px;
  }
  .back__brand .brand-dot {
    width: 26px;
    height: 26px;
    background: var(--card-white);
  }
  .back__slogan {
    position: absolute;
    bottom: 32px;
    left: 0;
    right: 0;
    font-size: 26px;
  }
</style>
</head>
<body>
  <section class="card card--front" aria-label="Business card front">
    <h1 class="front__company">TAMARIND RIDGELINE MEDIA</h1>
    <p class="front__slogan">Your information gateway</p>
    <div class="front__brand"><span class="brand-dot"></span>Ridgeline Press</div>
    <div class="front__divider"></div>
    <div class="front__person">
      <p class="person__name">Owen Farsk</p>
      <p class="person__title">Director of Sales &amp; Marketing</p>
    </div>
    <address class="front__contact" style="font-style:normal">
      Phone: 604 317 8842<br>
      #2714 - 582 E. Halvern St.<br>
      Vancouver, B.C. V7K2R4 Canada
    </address>
    <p class="front__online">
      www.tamarindridgeline.biz<br>
      owen@tamarindridgeline.biz
    </p>
  </section>

  <section class="card card--back" aria-label="Business card back">
    <p class="back__url">www.tamarindridgeline.biz</p>
    <div class="back__brand"><span class="brand-dot"></span>Ridgeline Press</div>
    <p class="back__slogan">Your information gateway</p>
  </section>
</body>
</html>
```